Martial Arts Website

Redevelopment of existing martial arts website.

The academy teaches traditional shaolin martial arts, including Shaolin Kung Fu, Wu Shu, Tai Chi, Qigong and Wing Chun and the site needs to reflect the traditional roots (eg, no tacky boxing imagery)

Existing website is www.copperlantern.com.au to get a feel for the desired color scheme (black, green and red). The exact colors can be tweaked though. Please only reuse the logo and font (Karate) - there isnt anything else from the current design that needs to remain.

The current website includes links to a ClipHarbor channel that includes demonstrations of the training conducted to better guide the design.

The new website site map will be:
1. Home
2. Programs - summary page describing each form of training
a. Tiny Otters
b. Kids Kung Fu
c. Youth Kung Fu
d. Adults Kung Fu
e. Wing Chun
f. Tai Chi & Qigong
g. Weaponry Classes
h. 72 Arts of Shaolin Conditioning Program
i. Acrobatics and Wu Shu
j. Fitness Boxing
3. Timetable
4. Coaches - summary page describing all coaches
a. Sifu (Master)
b. Sihing Kit
c. Sihing Sam
d. Sihing Marcus
X. ... up to 10 or so coaches
5. Member Zone
6. Contact Us
Updates

Logo now attached to brief - sorry I only have it in PDF

Just to clarify, I am only expecting a PSD design - no HTML required

Reason: Thanks for the designs, we love a lot of them just require a little extra time to tweak the designs and establish the potential. Thanks for your understanding and efforts.

Target Market(s)

Parents, teenagers, young adults, adults, elderly

Industry/Entity Type

Training

Requirements
Must have
• Chinese kung fu dragon imagery throughout the background
Links to Chatterly and ClipHarbor channel
Promo/icon in the header "Try 2 free classes now"
Home page should include an embedded ClipHarbor video

```html
<!DOCTYPE html>
<html lang="en">
<head>
<meta charset="utf-8">
<title>Copper Lantern Martial Arts Academy – Coaches</title>
<link href="https://fonts.googleapis.com/css2?family=Arimo:ital,wght@0,400;0,700;1,400;1,700&family=Tinos:wght@700&family=Bangers&display=swap" rel="stylesheet">
<style>
:root{
  --black:#000;
  --green:#1f7a1f;
  --green-dark:#0f4f10;
  --green-text:#1c6b1c;
  --red:#a50000;
  --red-bright:#d0100e;
  --grey:#555;
  --text:#222;
  --white:#fff;
  --rule:#9a9a9a;
}
*{margin:0;padding:0;box-sizing:border-box}
html,body{width:1095px;height:1200px;overflow:hidden;background:var(--black)}
body{position:relative;font-family:"Arimo",Arial,sans-serif;color:var(--text)}
.abs{position:absolute}

/* header */
.site-header{left:0;top:0;width:1095px;height:181px;background:var(--black)}
.brand{left:0;top:60px;width:1095px;text-align:center}
.brand-name{font-family:"Tinos",serif;font-weight:700;font-size:50px;letter-spacing:3px;color:#1d8a23;line-height:1}
.brand-mark{display:inline-block;width:26px;height:26px;border-radius:50%;background:#1d8a23;vertical-align:middle;margin:0 14px 8px}
.brand-sub{left:0;top:130px;width:1095px;text-align:center;font-family:"Tinos",serif;font-weight:700;color:var(--red-bright);font-size:16px;letter-spacing:4px}
.brand-tag{left:0;top:150px;width:1095px;text-align:center;color:#fff;font-size:10px;letter-spacing:2px}

/* nav */
.main-nav{left:0;top:181px;width:1095px;height:36px;background:var(--white)}
.main-nav a{position:absolute;top:0;height:36px;line-height:36px;font-size:12px;color:#444;text-decoration:none}
.main-nav .sep{position:absolute;top:6px;width:1px;height:24px;background:#ccc}
.main-nav .active{background:var(--red);color:#fff;top:-14px;height:50px;line-height:64px;padding:0 10px}

/* green band */
.section-band{left:0;top:217px;width:1095px;height:56px;background:linear-gradient(#258a26,#1a6d1b)}
.section-title{left:314px;top:230px;font-family:"Bangers",cursive;font-size:28px;color:#fff;letter-spacing:1px}
.sub-nav{left:421px;top:240px;font-size:14px;color:#fff}
.sub-nav .current{color:var(--red-bright);font-weight:700}
.sub-nav span.div{margin:0 7px}

/* side backgrounds */
.bg-left{left:0;top:273px;width:162px;height:651px;background:linear-gradient(#2a2a2a,#111)}
.bg-right{left:931px;top:627px;width:164px;height:297px;background:linear-gradient(#181818,#2c2c2c)}

/* content */
.content{left:162px;top:273px;width:769px;height:651px;background:var(--white)}
.crumbs{left:213px;top:286px;font-size:12px;color:#444}
.crumbs span{margin:0 7px}
.page-title{left:213px;top:334px;font-family:"Bangers",cursive;font-size:26px;color:var(--green-text);letter-spacing:1px}
.coach-photo{width:103px;background:linear-gradient(#b7a78f,#6b5a44)}
.coach-name{font-size:14.5px;font-weight:700;font-style:italic;color:#111}
.coach-bio{font-size:13px;line-height:17px;color:#222;width:470px}
.divider{left:176px;width:684px;border-top:1px dotted var(--rule)}

/* sidebar */
.sidebar{left:881px;top:217px;width:201px;height:410px;background:linear-gradient(#8a8a8a,#4d4d4d)}
.sidebar h2{position:absolute;left:0;top:10px;width:201px;text-align:center;font-family:"Tinos",serif;font-size:18px;color:#fff}
.sidebar .rule{position:absolute;left:24px;top:36px;width:152px;border-top:1px dotted #ccc}
.class-item{position:absolute;left:18px}
.class-item .dot{position:absolute;left:0;top:2px;width:15px;height:15px;border-radius:50%;background:var(--red-bright);box-shadow:0 0 0 2px #333}
.class-item .dot svg{position:absolute;left:3px;top:3px}
.class-item b{position:absolute;left:31px;top:0;white-space:nowrap;font-size:12px;font-style:italic;color:#fff}
.class-item i{position:absolute;left:31px;top:14px;white-space:nowrap;font-size:9.5px;color:#eee}
.cta{left:881px;top:599px;width:201px;height:28px;background:linear-gradient(#3a9a28,#1e6d12);color:#fff;font-weight:700;font-size:12.5px;line-height:28px;padding-left:11px}

/* red band + footer */
.red-band{left:0;top:924px;width:1095px;height:24px;background:var(--red)}
.footer{left:0;top:948px;width:1095px;height:169px;background:var(--white)}
.foot-head{font-family:"Tinos",serif;font-weight:700;font-size:15px;color:#222;top:964px}
.foot-div{top:964px;height:137px;border-left:1px dotted #888}
.foot-item{font-size:10.5px;line-height:12px;color:#222}
.foot-item b{display:block}
.badge{border-radius:4px}
.copyright{left:4px;top:1164px;font-size:11.5px;color:#777}
.copy-rule{left:4px;top:1152px;width:1066px;border-top:1px dotted #333}
</style>
</head>
<body>

<header class="site-header abs">
  <div class="brand abs"><span class="brand-name">COPPER</span><span class="brand-mark"></span><span class="brand-name">LANTERN</span></div>
  <div class="brand-sub abs">MARTIAL ARTS ACADEMY</div>
  <div class="brand-tag abs">TRADITIONAL KUNG FU &amp; TAI CHI TRAINING CENTRE</div>
</header>

<nav class="main-nav abs">
  <a style="left:283px">HOME</a><span class="sep" style="left:343px"></span>
  <a style="left:360px">PROGRAMS</a><span class="sep" style="left:440px"></span>
  <a style="left:456px">TIMETABLE</a><span class="sep" style="left:532px"></span>
  <a class="active" style="left:542px">COACHES</a><span class="sep" style="left:627px"></span>
  <a style="left:642px">MEMBER ZONE</a><span class="sep" style="left:744px"></span>
  <a style="left:758px">CONTACT US</a>
</nav>

<div class="section-band abs"></div>
<div class="section-title abs">COACHES</div>
<div class="sub-nav abs"><span class="current">Shaolin Chuan Fa</span><span class="div">|</span>Tai Chi &amp; Qigong<span class="div">|</span>Wing Chun</div>

<div class="bg-left abs" role="img" aria-label="Dark background of faint Chinese calligraphy"></div>
<div class="bg-right abs" role="img" aria-label="Dark background of faint Chinese calligraphy"></div>

<main class="content abs"></main>
<div class="crumbs abs">Home<span>&gt;</span>Coaches<span>&gt;</span>Shaolin Chuan Fa</div>
<h1 class="page-title abs">SHAOLIN CHUAN FA (KUNG FU)</h1>

<div class="coach-photo abs" style="left:214px;top:381px;height:145px" role="img" aria-label="Head instructor in a high kicking stance outdoors"></div>
<div class="coach-name abs" style="left:337px;top:380px">Owen Hartley – Sifu (Master – Head Instructor)</div>
<p class="coach-bio abs" style="left:337px;top:405px">Personal student of Grandmaster Shi Wen Lu - 31st Generation Shaolin Warrior Monk. Trained under the direct guidance of Sigong Colin Avery to the level of “Sifu” and further to the level of Red Sash (master) in the traditional Chuan Fa system. Trained with Master Liang Po (Chinese WuShu champion), Master Fen Jia Ming (World WuShu champion), and trained at the Shaolin Temple with Shi Wen Kai (31st generation monk).</p>
<div class="divider abs" style="top:555px"></div>

<div class="coach-photo abs" style="left:214px;top:585px;height:144px" role="img" aria-label="Senior instructor performing a side kick by a stone wall"></div>
<div class="coach-name abs" style="left:337px;top:584px">Kit Ashford – Sihing (Senior Student - Senior Instructor)</div>
<p class="coach-bio abs" style="left:337px;top:609px">Trained under Sifu Owen Hartley to the level of Black Sash “Sihing” in the traditional Chuan Fa system. Trained at the Shaolin Temple with Shi Wen Kai (31st generation monk).</p>
<div class="divider abs" style="top:753px"></div>

<div class="coach-photo abs" style="left:214px;top:772px;height:141px" role="img" aria-label="Senior instructor in a low horse stance on training posts"></div>
<div class="coach-name abs" style="left:335px;top:774px">Sam Tolliver – Sihing (Senior Student - Senior Instructor)</div>
<p class="coach-bio abs" style="left:335px;top:799px">Trained under Sifu Owen Hartley to the level of Black Sash “Sihing” in the traditional Chuan Fa system. Trained at the Shaolin Temple with Shi Wen Kai (31st generation monk).</p>

<aside class="sidebar abs">
  <h2>ALL CLASSES</h2><div class="rule"></div>
  <div class="class-item" style="top:50px"><span class="dot"><svg width="9" height="9" viewBox="0 0 9 9"><path d="M0 3h5V0l4 4.5L5 9V6H0z" fill="#fff"/></svg></span><b>Tiny Otters</b><i>Ages 4 - 6</i></div>
  <div class="class-item" style="top:85px"><span class="dot"><svg width="9" height="9" viewBox="0 0 9 9"><path d="M0 3h5V0l4 4.5L5 9V6H0z" fill="#fff"/></svg></span><b>Kids Kung Fu</b><i>Ages 6 - 11</i></div>
  <div class="class-item" style="top:120px"><span class="dot"><svg width="9" height="9" viewBox="0 0 9 9"><path d="M0 3h5V0l4 4.5L5 9V6H0z" fill="#fff"/></svg></span><b>Youth Kung Fu</b><i>Ages 11 - 15</i></div>
  <div class="class-item" style="top:153px"><span class="dot"><svg width="9" height="9" viewBox="0 0 9 9"><path d="M0 3h5V0l4 4.5L5 9V6H0z" fill="#fff"/></svg></span><b>Adults Kung Fu</b><i>Ages 15 &amp; over</i></div>
  <div class="class-item" style="top:188px"><span class="dot"><svg width="9" height="9" viewBox="0 0 9 9"><path d="M0 3h5V0l4 4.5L5 9V6H0z" fill="#fff"/></svg></span><b>Wing Chun</b><i>Ages 13 &amp; over</i></div>
  <div class="class-item" style="top:223px"><span class="dot"><svg width="9" height="9" viewBox="0 0 9 9"><path d="M0 3h5V0l4 4.5L5 9V6H0z" fill="#fff"/></svg></span><b>Tai Chi &amp; Qigong</b><i>All ages</i></div>
  <div class="class-item" style="top:257px"><span class="dot"><svg width="9" height="9" viewBox="0 0 9 9"><path d="M0 3h5V0l4 4.5L5 9V6H0z" fill="#fff"/></svg></span><b>Weaponry Classes</b><i>Ages 5 and over</i></div>
  <div class="class-item" style="top:292px"><span class="dot"><svg width="9" height="9" viewBox="0 0 9 9"><path d="M0 3h5V0l4 4.5L5 9V6H0z" fill="#fff"/></svg></span><b>72 Arts of Shaolin</b><i>Conditioning Program</i></div>
  <div class="class-item" style="top:327px"><span class="dot"><svg width="9" height="9" viewBox="0 0 9 9"><path d="M0 3h5V0l4 4.5L5 9V6H0z" fill="#fff"/></svg></span><b>Acrobatics and Wu Shu</b><i>Performance Team</i></div>
  <div class="class-item" style="top:361px"><span class="dot"><svg width="9" height="9" viewBox="0 0 9 9"><path d="M0 3h5V0l4 4.5L5 9V6H0z" fill="#fff"/></svg></span><b>Fitness Boxing</b></div>
</aside>
<div class="cta abs">TRY 2 FREE CLASSES NOW! <svg width="9" height="13" viewBox="0 0 9 13" style="vertical-align:-2px;margin-left:5px"><path d="M0 0l9 6.5L0 13z" fill="#fff"/></svg></div>

<div class="red-band abs"></div>
<footer class="footer abs"></footer>

<h3 class="foot-head abs" style="left:64px">Contact</h3>
<h3 class="foot-head abs" style="left:334px">News &amp; Downloads</h3>
<h3 class="foot-head abs" style="left:632px">Social Media</h3>
<h3 class="foot-head abs" style="left:860px">Alliances &amp; Accreditation</h3>
<div class="foot-div abs" style="left:253px"></div>
<div class="foot-div abs" style="left:547px"></div>
<div class="foot-div abs" style="left:820px"></div>

<svg class="abs" style="left:36px;top:1006px" width="14" height="24" viewBox="0 0 14 24"><rect x="1" y="1" width="12" height="22" rx="2" fill="none" stroke="#555" stroke-width="2"/><rect x="3.5" y="4" width="7" height="12" fill="#555"/><circle cx="7" cy="19.5" r="1.3" fill="#555"/></svg>
<div class="foot-item abs" style="left:64px;top:1007px"><b>Phone:</b>(02) 5550 1234</div>
<svg class="abs" style="left:28px;top:1048px" width="24" height="16" viewBox="0 0 24 16"><rect x="1" y="1" width="22" height="14" fill="none" stroke="#555" stroke-width="1.6"/><path d="M1 1l11 8 11-8M1 15l8-7M23 15l-8-7" fill="none" stroke="#555" stroke-width="1.4"/></svg>
<div class="foot-item abs" style="left:64px;top:1045px"><b>Email:</b>kwoon@copperlantern.com.au</div>

<svg class="abs" style="left:305px;top:1009px" width="18" height="20" viewBox="0 0 18 20"><rect x="1" y="1" width="12" height="15" fill="#888"/><rect x="4" y="4" width="12" height="15" fill="#666"/></svg>
<div class="foot-item abs" style="left:336px;top:1007px"><b>Newsletter</b>Click here to download</div>
<svg class="abs" style="left:305px;top:1044px" width="19" height="19" viewBox="0 0 19 19"><circle cx="9.5" cy="9.5" r="7.5" fill="none" stroke="#666" stroke-width="2"/><circle cx="9.5" cy="9.5" r="3" fill="none" stroke="#666" stroke-width="2"/></svg>
<div class="foot-item abs" style="left:336px;top:1045px"><b>News &amp; Updates</b>Click here to view</div>

<svg class="abs" style="left:591px;top:1005px" width="30" height="30" viewBox="0 0 30 30"><rect width="30" height="30" rx="4" fill="#777"/><path d="M11 9l10 6-10 6z" fill="#fff"/></svg>
<div class="foot-item abs" style="left:646px;top:1007px"><b>ClipHarbor</b>View our channel here</div>
<svg class="abs" style="left:591px;top:1042px" width="30" height="30" viewBox="0 0 30 30"><rect width="30" height="30" rx="4" fill="#3a5a98"/><path d="M7 9h16v10H14l-5 4v-4H7z" fill="#fff"/></svg>
<div class="foot-item abs" style="left:646px;top:1045px"><b>Chatterly</b></div>
<div class="foot-item abs" style="left:633px;top:1060px;width:130px"><span style="display:inline-block;width:10px;height:10px;background:#3a5a98;vertical-align:-1px;margin-right:3px"></span>222 people like this. Be<br><span style="padding-left:13px">the first of your friends.</span></div>
<div class="abs" style="left:596px;top:1080px;width:47px;height:21px;border:1px solid #ccd;background:#eef0f5;border-radius:2px;font-size:10.5px;line-height:19px;text-align:center;color:#3a5a98">Like</div>

<div class="badge abs" style="left:897px;top:991px;width:61px;height:44px;background:#8a8a8a"></div>
<div class="abs" style="left:975px;top:990px;width:47px;height:47px;border-radius:50%;background:#c21010;border:3px solid #111"></div>
<div class="abs" style="left:893px;top:1044px;width:68px;height:40px;border-radius:50%;border:3px solid #111;background:#fff"></div>
<div class="abs" style="left:981px;top:1042px;width:36px;height:36px;border-radius:50%;background:#1f4fa0"></div>

<div class="copy-rule abs"></div>
<div class="copyright abs">Copyright © 2012 - Copper Lantern Martial Arts Pty Ltd. Kung Fu and Tai Chi Training Centre - Unit 4, 22 Harbour Lane, Westvale NSW 2999</div>

</body>
</html>
```